The Harbourlight Dental centre, the Zorvik of dentistry

New concept of running a dental practice by having a walk in practice
WE ARE A HUSBAND AND WIFE TEAM

Really modern and sophisticated, we want it to feel different from the traditional dental practice.
we want it split into different pages:CONTACT US
LOCATION: Information about our location since patients often confuse us with the practice across the road
ABOUT US:
Opening hours - & 7 Days, We offer a weekend service
WALK IN: We offer a walk in service for dental treatments
TREATMENTS we offer

DENTAL ADVICE: Free dentist advise call back- So a dentist will call you back for free to discuss

Target Market(s)

Everyone

Industry/Entity Type

Dental

Coding

Coded - Design and coding required

Number of Pages Required

5+ page

Requirements
Must have
• First page
• * changing pictures
• *opening times
• * our walk in concept I.e. no appointment needed
• *logo
• * links in to clinic tidal (online booking system in Australia)
• * address /phone number/email
• * possible videos
• Second page
• meet the team
• third page
• dental treatments/walk in treatments
• fourth page
• dental advice with vid larko videos
• Fifth page
• contact us/maps/ we get confused with the dental practice across the road
• We would also like a giving back page. In this please include the photo's below of our dental mission in Guatemala, where by we did treatment for patients as part of a charity.
Nice to have
• Changing pictures on the home screen
• videos linked to home page

```html
<!DOCTYPE html>
<html lang="en">
<head>
<meta charset="utf-8">
<title>The Harbourlight Dental Centre</title>
<link rel="stylesheet" href="https://fonts.googleapis.com/css2?family=Raleway:wght@400;500;600;700;800&display=swap">
<style>
:root{
  --blue:#1ab0e6;
  --blue-dark:#0f9fd6;
  --green:#8cc63f;
  --green-dark:#6fa82a;
  --text:#555;
  --text-light:#777;
  --dark:#4a4a4a;
  --darker:#353535;
  --light-bg:#f5f5f5;
  --white:#fff;
}
*{box-sizing:border-box;margin:0;padding:0}
html,body{width:1200px;height:2214px;overflow:hidden}
body{position:relative;font-family:"Raleway",sans-serif;color:var(--text);background:var(--white)}
.abs{position:absolute}
.topline{left:0;top:0;width:1200px;height:4px;background:linear-gradient(90deg,var(--green) 50%,var(--blue) 50%)}
.brand{display:flex;align-items:center;gap:10px}
.brand-mark{width:30px;height:30px;border-radius:50%;background:var(--blue)}
.brand-name{font-weight:700;font-size:21px;color:var(--green);line-height:1}
.brand-sub{font-size:8px;letter-spacing:2px;color:var(--green);font-weight:600;margin-top:3px}
.header-info h4{font-size:11.5px;font-weight:700;color:var(--green);text-transform:uppercase;margin-bottom:10px}
.header-info p{font-size:12.5px;font-weight:600;color:#444;line-height:21px;display:flex;align-items:center;gap:8px}
.nav{left:0;top:108px;width:1200px;height:46px;background:var(--blue)}
.nav a{position:absolute;top:16px;font-size:12px;font-weight:700;color:var(--white);text-decoration:none;text-transform:uppercase}
.hero{left:0;top:154px;width:1200px;height:478px;background:linear-gradient(100deg,#5e8a3c 0%,#8fae63 30%,#c9b79c 55%,#e7d2b4 75%,#c4d39a 100%)}
.hero h1{left:76px;top:92px;font-size:51px;line-height:48px;font-weight:800;color:var(--white)}
.hero h2{left:76px;top:204px;font-size:30px;line-height:40px;font-weight:700;color:var(--white)}
.hero .note{left:76px;top:300px;font-size:12.5px;font-weight:700;color:var(--white)}
.tidal-btn{display:flex;align-items:center;gap:8px;font-size:22px;font-weight:500;color:var(--white)}
.tidal-btn .sq{width:22px;height:22px;background:var(--white)}
.hero .tidal-btn{left:75px;top:324px;width:215px;height:47px;background:var(--green);padding-left:14px}
.dots{left:75px;top:422px;display:flex;gap:9px}
.dots span{width:11px;height:11px;border-radius:50%;background:#6a6a6a}
.dots span:first-child{background:var(--blue)}
.section-title{font-size:21px;font-weight:700;color:var(--blue);text-transform:uppercase}
.welcome h2{left:0;top:680px;width:1200px;text-align:center}
.welcome p{left:80px;top:728px;width:1040px;text-align:center;font-size:14px;line-height:26.5px;color:var(--text-light)}
.btn{display:flex;align-items:center;justify-content:center;background:linear-gradient(var(--green),var(--green-dark));color:var(--white);font-size:13px;font-weight:700;text-transform:uppercase;border-radius:2px}
.treatments{left:0;top:950px;width:1200px;height:448px;background:var(--light-bg)}
.treatments h2{left:0;top:45px;width:1200px;text-align:center}
.card{top:100px;width:242px}
.card .photo{width:242px;height:168px}
.card h3{font-size:16px;font-weight:700;color:var(--green);margin-top:22px}
.card p{font-size:13.5px;line-height:23px;color:var(--text-light);margin-top:6px;padding-right:10px}
.team-text{left:304px;top:1484px;width:380px;font-size:14px;line-height:26.5px;color:var(--text-light)}
.video{left:704px;top:1490px;width:422px;height:268px;background:linear-gradient(135deg,#5a5f58,#8a8270 45%,#3d3d3d)}
.banner{left:0;top:1795px;width:1200px;height:88px;background:var(--blue)}
.banner .slogan{left:158px;top:37px;font-size:13.5px;font-weight:700;color:var(--white);text-transform:uppercase}
.banner .tidal-btn{left:654px;top:19px;width:212px;height:50px;border:2px solid var(--white);padding-left:14px}
.banner .note{left:878px;top:37px;font-size:13px;font-weight:700;color:var(--white)}
.footer{left:0;top:1883px;width:1200px;height:272px;background:var(--dark);color:#ddd}
.footer h4{font-size:13px;font-weight:600;color:var(--green);text-transform:uppercase}
.footer .col{top:42px}
.footer ul{list-style:none;margin-top:14px}
.footer li{font-size:12.5px;line-height:31px;color:#e5e5e5}
.footer p{font-size:12.5px;line-height:22px;color:#e5e5e5}
.footer strong{font-size:12px;font-weight:700;color:var(--white);text-transform:uppercase}
.socials{display:flex;gap:6px;margin-top:16px}
.socials span{width:29px;height:29px;border-radius:50%}
.copyright{left:0;top:2155px;width:1200px;height:59px;background:var(--darker);text-align:center;line-height:59px;font-size:12.5px;color:#aaa}
</style>
</head>
<body>
<div class="abs topline"></div>

<header>
  <div class="abs brand" style="left:75px;top:34px">
    <span class="brand-mark"></span>
    <div><div class="brand-name">The Harbourlight</div><div class="brand-sub">DENTAL CENTRE</div></div>
  </div>
  <div class="abs header-info" style="left:730px;top:26px">
    <h4>Contact Address:</h4>
    <p><svg width="12" height="12" viewBox="0 0 24 24"><path fill="#444" d="M6.6 10.8a15.1 15.1 0 0 0 6.6 6.6l2.2-2.2a1 1 0 0 1 1-.25 11.4 11.4 0 0 0 3.6.6 1 1 0 0 1 1 1V20a1 1 0 0 1-1 1A17 17 0 0 1 3 4a1 1 0 0 1 1-1h3.5a1 1 0 0 1 1 1c0 1.25.2 2.45.6 3.6a1 1 0 0 1-.25 1z"/></svg>08 5550 2718</p>
    <p><svg width="12" height="10" viewBox="0 0 24 18"><rect width="24" height="18" rx="2" fill="#444"/><path d="M1 2l11 8 11-8" stroke="#fff" stroke-width="2" fill="none"/></svg>info@harbourlightdental.com</p>
  </div>
  <div class="abs header-info" style="left:948px;top:26px">
    <h4>Opening Hours:</h4>
    <p>Open 8 Am To 8pm 7 Days</p>
    <p>A Week</p>
  </div>
</header>

<nav class="abs nav">
  <a style="left:76px">Home</a>
  <a style="left:180px">About Team</a>
  <a style="left:331px">Dental Treatments</a>
  <a style="left:540px">Dental Advice</a>
  <a style="left:708px">Clinic Tidal</a>
  <a style="left:878px">Contact Us</a>
</nav>

<section class="abs hero" role="img" aria-label="Slideshow photo of a smiling mother and daughter outdoors">
  <h1 class="abs">The Harbourlight<br>Dental Care</h1>
  <h2 class="abs">We offer a walk in service for<br>dental treatments</h2>
  <div class="abs note">No Need of Appointmet</div>
  <div class="abs tidal-btn"><span class="sq"></span>Clinic Tidal</div>
  <div class="abs dots"><span></span><span></span><span></span><span></span></div>
</section>

<section class="welcome">
  <h2 class="abs section-title">Welcome to our website</h2>
  <p class="abs">Aliquam molestie, mi et imperdiet euismod, dui purus auctor tellus, et interdum lacus lectus et ante. Sed accumsan sollicitudin sapien, sit amet adipiscing turpis gravida ac. In congue, neque ac lobortis volutpat, libero mauris varius mi, vitae suscipit ipsum ligula vitae risus. Duis aliquam nibh a dui iaculis viverra id a velit. Vivamus egestas risus in magna varius commodo. Sed semper viverra egestas. Etiam pretium porttitor lectus, vel ornare neque porta volutpat.</p>
  <div class="abs btn" style="left:524px;top:869px;width:152px;height:44px">Read More</div>
</section>

<section class="abs treatments">
  <h2 class="abs section-title">Treatments we offer</h2>
  <div class="abs card" style="left:75px">
    <div class="photo" role="img" aria-label="Close-up photo of a tooth with a filling" style="background:linear-gradient(135deg,#c24a3a,#e8c9b8 55%,#a33b2e)"></div>
    <h3>Fillings</h3>
    <p>Technological advances have rendered cosmetic white fillings as strong and reliable as the traditional mercury..</p>
  </div>
  <div class="abs card" style="left:344px">
    <div class="photo" role="img" aria-label="Photo of a patient receiving root canal treatment" style="background:linear-gradient(135deg,#b9c4c9,#8d9aa0 50%,#5f8fa0)"></div>
    <h3>Root Canal Treatment</h3>
    <p>Root canal therapy (RCT) is a technique used to retain a tooth with an irreversibly damaged nerve...</p>
  </div>
  <div class="abs card" style="left:615px">
    <div class="photo" role="img" aria-label="Before and after photo of whitened teeth" style="background:linear-gradient(180deg,#f1d9cf,#d9756e 45%,#f4ece6 60%,#e9b7a9)"></div>
    <h3>Teeth Whitening</h3>
    <p>Now you can whiten your smile with our custom fitted whitening trays in the comfort of your own home..</p>
  </div>
  <div class="abs card" style="left:884px">
    <div class="photo" role="img" aria-label="Photo of a dental crown model" style="background:linear-gradient(135deg,#e86aa8,#f3b2cf 50%,#d14e8d)"></div>
    <h3>Crowns and Bridges</h3>
    <p>A crown (cap) is a covering that encases the entire tooth surface, thus restoring it to its original shape, size, and colour..</p>
  </div>
</section>

<section class="team">
  <h2 class="abs section-title" style="left:75px;top:1438px">Meet the team</h2>
  <div class="abs" role="img" aria-label="Photo of the husband and wife dentist team" style="left:75px;top:1490px;width:211px;height:268px;background:linear-gradient(180deg,#e9e4de,#5e8fb5 55%,#2f4f48)"></div>
  <p class="abs team-text">Aliquam molestie, mi et imperdiet euismod, dui purus auctor tellus, et interdum lacus lectus et ante. Sed accumsan sollicitudin sapien, sit amet adipiscing turpis gravida ac. In congue, neque ac lobortis volutpat, libero mauris varius mi, vitae suscipit ipsum ligula vitae risus. Duis aliquam nibh a dui iaculis viverra id a velit. Vivamus egestas risus in magna varius commodo.</p>
  <div class="abs btn" style="left:303px;top:1715px;width:151px;height:44px">Read More</div>
</section>

<section class="advice">
  <h2 class="abs section-title" style="left:704px;top:1438px">Dental advice</h2>
  <div class="abs video" role="img" aria-label="Video still from the dental mission in Guatemala">
    <svg class="abs" style="left:184px;top:107px" width="54" height="54" viewBox="0 0 54 54"><circle cx="27" cy="27" r="24" fill="none" stroke="#fff" stroke-width="4"/><path d="M21 16l17 11-17 11z" fill="#fff"/></svg>
  </div>
</section>

<section class="abs banner">
  <div class="abs slogan">Aenean a nibh eget turpis vehicula tempus ac sed massa.</div>
  <div class="abs tidal-btn"><span class="sq"></span>Clinic Tidal</div>
  <div class="abs note">No Need of Appointmet</div>
</section>

<footer class="abs footer">
  <div class="abs brand" style="left:75px;top:40px">
    <span class="brand-mark" style="background:#ddd"></span>
    <div><div class="brand-name" style="color:#fff">The Harbourlight</div><div class="brand-sub" style="color:#ddd">DENTAL CENTRE</div></div>
  </div>
  <p class="abs" style="left:75px;top:122px;width:300px">Duis aliquam nibh a dui iaculis viverra id a velit. Vivamus egestas risus in magna varius commodo. Sed semper viverra egestas.</p>
  <p class="abs" style="left:75px;top:206px;color:var(--green)">Learn More</p>

  <div class="abs col" style="left:434px">
    <h4>Quick Links</h4>
    <ul><li>Home</li><li>About Team</li><li>Dental Treatments</li><li>Dental Advice</li><li>Clinic Tidal</li><li>Contact Us</li></ul>
  </div>
  <div class="abs col" style="left:624px">
    <h4>Contact Us</h4>
    <p style="margin-top:14px"><strong>Harbourlight Dental Centre</strong><br>Unit 4, 38 Tidewater Boulevard,<br>Seabrook, WA 6000.</p>
    <p style="margin-top:10px">&#9742;&nbsp; 08 5550 2718<br>&#9993;&nbsp; info@harbourlightdental.com<br>
    <svg width="9" height="12" viewBox="0 0 12 16"><path d="M6 0a6 6 0 0 0-6 6c0 4.5 6 10 6 10s6-5.5 6-10a6 6 0 0 0-6-6zm0 8.5A2.5 2.5 0 1 1 6 3.5a2.5 2.5 0 0 1 0 5z" fill="#e5e5e5"/></svg>&nbsp; Get Map Direction</p>
  </div>
  <div class="abs col" style="left:885px">
    <h4>Opening Times</h4>
    <p style="margin-top:14px"><strong>Open 8 am to 8pm 7 days a week</strong></p>
    <h4 style="margin-top:42px">Connect Us</h4>
    <div class="socials">
      <span style="background:#3b5998"></span><span style="background:#1da1f2"></span><span style="background:#3a3a3a"></span><span style="background:#cb2027"></span><span style="background:#dd4b39"></span><span style="background:#e62117"></span>
    </div>
  </div>
</footer>

<div class="abs copyright">Copyright © 2016. Company Name All Right Reserved</div>
</body>
</html>
```